Sparrow Haulage needs a business card design.

Design a double-sided business card for new freight business. On the front, would like to see our logo along with the following info:

Martin Obuya
CEO/FOUNDER
555-206-7142
martinobuya@sparrow-haulage.example

On the reverse side, we would like to use the graphic image of our logo only without the Sparrow Haulage name.

```html
<!DOCTYPE html>
<html lang="en">
<head>
<meta charset="utf-8">
<title>Sparrow Haulage – Business Card</title>
<link href="https://fonts.googleapis.com/css2?family=Open+Sans:wght@400;700&display=swap" rel="stylesheet">
<style>
  :root {
    --navy: #1f1b5c;
    --navy-deep: #211c55;
    --navy-soft: #29225e;
    --red: #c0262d;
    --paper: #ffffff;
    --backdrop: #d9d9dc;
    --ink: #1f1b5c;
  }
  * { margin: 0; padding: 0; box-sizing: border-box; }
  html, body {
    width: 1200px;
    height: 900px;
    overflow: hidden;
    background: var(--backdrop);
    font-family: "Open Sans", sans-serif;
  }
  .sheet {
    width: 1200px;
    height: 900px;
    display: flex;
    flex-direction: column;
    align-items: center;
    justify-content: center;
    gap: 56px;
  }
  .card {
    width: 630px;
    height: 360px;
    position: relative;
    box-shadow: 0 6px 18px rgba(0,0,0,0.18);
  }

  /* Reverse side: mark only */
  .card--back {
    background: linear-gradient(160deg, var(--navy-deep), var(--navy-soft));
    display: flex;
    align-items: center;
    justify-content: center;
  }
  .back-mark {
    width: 64px;
    height: 64px;
    background: var(--red);
  }

  /* Front side */
  .card--front { background: var(--paper); }
  .brand {
    position: absolute;
    left: 36px;
    top: 150px;
    display: flex;
    align-items: center;
    gap: 10px;
    color: var(--navy);
    font-weight: 700;
    font-size: 26px;
    white-space: nowrap;
  }
  .brand .mark-square {
    width: 18px;
    height: 18px;
    background: var(--navy);
  }
  .divider {
    position: absolute;
    left: 296px;
    top: 108px;
    width: 2px;
    height: 134px;
    background: var(--navy);
  }
  .contact {
    position: absolute;
    left: 314px;
    top: 106px;
    color: var(--ink);
    white-space: nowrap;
  }
  .contact .person {
    color: var(--red);
    font-weight: 700;
    font-size: 22px;
    line-height: 1.1;
  }
  .contact .role {
    font-size: 16px;
    line-height: 1.3;
    margin-bottom: 14px;
  }
  .contact-list { list-style: none; }
  .contact-list li {
    display: flex;
    align-items: center;
    gap: 8px;
    font-size: 14px;
    line-height: 1.6;
  }
  .contact-list svg {
    width: 14px;
    height: 14px;
    flex: none;
  }
</style>
</head>
<body>
  <main class="sheet">
    <section class="card card--back" aria-label="Card reverse">
      <div class="back-mark" role="img" aria-label="Sparrow Haulage mark"></div>
    </section>

    <section class="card card--front" aria-label="Card front">
      <div class="brand">
        <span class="mark-square"></span>
        <span>Sparrow Haulage</span>
      </div>
      <div class="divider"></div>
      <div class="contact">
        <p class="person">Martin Obuya</p>
        <p class="role">CEO/FOUNDER</p>
        <ul class="contact-list">
          <li>
            <svg viewBox="0 0 24 24" aria-hidden="true"><path fill="#c0262d" d="M6.6 10.8a15.1 15.1 0 0 0 6.6 6.6l2.2-2.2a1 1 0 0 1 1-.25 11.4 11.4 0 0 0 3.6.57 1 1 0 0 1 1 1V20a1 1 0 0 1-1 1A17 17 0 0 1 3 4a1 1 0 0 1 1-1h3.5a1 1 0 0 1 1 1c0 1.25.2 2.45.57 3.57a1 1 0 0 1-.25 1z"/></svg>
            <span>555-206-7142</span>
          </li>
          <li>
            <svg viewBox="0 0 24 24" aria-hidden="true"><rect x="2.5" y="5" width="19" height="14" fill="none" stroke="#c0262d" stroke-width="2"/><path d="M3 6l9 7 9-7M3 18l7-6M21 18l-7-6" fill="none" stroke="#c0262d" stroke-width="1.8"/></svg>
            <span>martinobuya@sparrow-haulage.example</span>
          </li>
          <li>
            <svg viewBox="0 0 24 24" aria-hidden="true"><g fill="none" stroke="#c0262d" stroke-width="1.8"><circle cx="12" cy="12" r="9.5"/><ellipse cx="12" cy="12" rx="4.2" ry="9.5"/><path d="M2.5 12h19M4 7h16M4 17h16"/></g></svg>
            <span>www.sparrow-haulage.example</span>
          </li>
        </ul>
      </div>
    </section>
  </main>
</body>
</html>
```